Business Card for Coastal Tundrabridge Advisory

We need a business card for Coastal Tundrabridge Advisory. The company website address is provided below. The company logo is attached. We provide specialized permafrost services to the mining, transportation, and oil & gas industries. The card should be prepared for:
Matthias Korhonen, PhD.
Coastal Tundrabridge Advisory
PO Box 418259
Quillwater, Alaska 99642
Direct: +1-907-555-0143
Email: mkorhonen@tundrabridgeadvisory.example
Website: www.coastaltundrabridgeadvisory.example

```html
<!DOCTYPE html>
<html lang="en">
<head>
<meta charset="utf-8">
<title>Coastal Tundrabridge Advisory – Business Card</title>
<link rel="stylesheet" href="https://fonts.googleapis.com/css2?family=Montserrat:wght@400;500;600;700&display=swap">
<style>
  :root {
    --backdrop: #d9d6d1;
    --paper: #ffffff;
    --ink: #141a22;
    --ink-soft: #2a2a2a;
    --card-dark: #1f1f1f;
    --band-dark: #222222;
    --band-grey: #8e8e8e;
    --rule: #1a1a1a;
    --on-dark: #ffffff;
  }
  * { margin: 0; padding: 0; box-sizing: border-box; }
  html, body {
    width: 900px; height: 1200px; overflow: hidden;
    background: var(--backdrop);
    font-family: "Montserrat", sans-serif;
  }
  .canvas { position: relative; width: 900px; height: 1200px; }

  .card {
    position: absolute; left: 80px; width: 740px; height: 440px;
    border-radius: 40px; overflow: hidden;
  }
  .card--front { top: 132px; background: var(--paper); color: var(--ink-soft); }
  .card--back { top: 640px; background: var(--card-dark); }

  .wordmark {
    position: absolute; font-weight: 600; text-transform: uppercase;
    letter-spacing: 3px; line-height: 1.2;
  }
  .card--front .wordmark {
    top: 56px; right: 52px; width: 400px; text-align: right;
    font-size: 24px; color: var(--ink);
  }
  .card--back .wordmark {
    top: 176px; left: 0; width: 100%; text-align: center;
    font-size: 30px; color: var(--on-dark);
  }

  .holder { position: absolute; left: 38px; top: 266px; }
  .holder__name { font-size: 26px; font-weight: 700; color: var(--ink); letter-spacing: -0.2px; }
  .holder__role { font-size: 16px; font-weight: 400; margin-top: 2px; }

  .rule { position: absolute; left: 38px; top: 326px; width: 670px; height: 1.5px; background: var(--rule); }

  .contacts { position: absolute; left: 38px; top: 343px; list-style: none; font-size: 16px; }
  .contacts li { display: flex; align-items: center; height: 22px; }
  .contacts svg { width: 14px; height: 14px; margin-right: 12px; fill: var(--ink-soft); }

  .address { position: absolute; left: 503px; top: 365px; font-size: 16px; line-height: 20px; }

  .band { position: absolute; left: 0; bottom: 0; width: 740px; height: 16px; }
</style>
</head>
<body>
<main class="canvas">
  <section class="card card--front">
    <div class="wordmark">Coastal Tundrabridge Advisory</div>

    <div class="holder">
      <div class="holder__name">Matthias Korhonen, PhD.</div>
      <div class="holder__role">CEO &amp; Founder</div>
    </div>

    <div class="rule"></div>

    <ul class="contacts">
      <li>
        <svg viewBox="0 0 16 16" aria-hidden="true"><path d="M1 6c0-2 3-3 7-3s7 1 7 3v1h-3V5.5H4V7H1z"/><rect x="3" y="8" width="10" height="6" rx="1"/></svg>
        +1-907-555-0143
      </li>
      <li>
        <svg viewBox="0 0 16 16" aria-hidden="true"><path d="M1 3h14v1.5L8 9 1 4.5z"/><path d="M1 6l7 4.5L15 6v7H1z"/></svg>
        mkorhonen@tundrabridgeadvisory.example
      </li>
      <li>
        <svg viewBox="0 0 16 16" aria-hidden="true"><circle cx="8" cy="8" r="7"/><path d="M5 4c1 1 2 1 2 3s-2 1-2 3 2 3 2 3" stroke="#fff" stroke-width="1.2" fill="none"/><path d="M10 3c0 2 2 2 2 4" stroke="#fff" stroke-width="1.2" fill="none"/></svg>
        www.coastaltundrabridgeadvisory.example
      </li>
    </ul>

    <div class="address">
      PO Box 418259<br>
      Quillwater, Alaska 99642
    </div>

    <svg class="band" viewBox="0 0 740 16" preserveAspectRatio="none" aria-hidden="true">
      <polygon points="0,0 496,0 484,16 0,16" fill="var(--band-dark)"/>
      <polygon points="506,0 740,0 740,16 494,16" fill="var(--band-grey)"/>
    </svg>
  </section>

  <section class="card card--back">
    <div class="wordmark">Coastal Tundrabridge Advisory</div>
  </section>
</main>
</body>
</html>
```